Dunmore Roofing

Want a professional looking business card

Industry/Entity Type

Business

Contact Information for Business Card

Paul Dunmore ( Owner) paul@dunmoreroofing-example.com, www.dunmoreroofing-example.com, Adress: 4172 Township road 43 Ridgeview,ON K9X4T2

```html
<!DOCTYPE html>
<html lang="en">
<head>
<meta charset="utf-8">
<title>Dunmore Roofing – Business Card</title>
<link rel="stylesheet" href="https://fonts.googleapis.com/css2?family=Montserrat:wght@400;500;700;800&display=swap">
<style>
  :root {
    --bg: #1a1a1c;
    --brand-blue: #1f4594;
    --brand-blue-dark: #253a86;
    --brand-navy: #1c2f78;
    --ink: #3a3a3a;
    --ink-soft: #555;
    --grey-band: #9a9a9a;
    --paper: #ffffff;
    --paper-shade: #f1f1f1;
    --back-ink: #e6e8ee;
  }
  * { box-sizing: border-box; margin: 0; padding: 0; }
  html, body { width: 1200px; height: 963px; overflow: hidden; }
  body {
    background: var(--bg);
    font-family: "Montserrat", sans-serif;
    display: flex;
    flex-direction: column;
    align-items: center;
    justify-content: center;
    gap: 56px;
  }
  .card {
    position: relative;
    width: 700px;
    height: 400px;
    border-radius: 18px;
    overflow: hidden;
  }

  /* Front */
  .card-front {
    background: linear-gradient(160deg, var(--paper-shade), var(--paper) 45%);
  }
  .front-swoosh { position: absolute; inset: 0; }
  .holder { position: absolute; left: 62px; top: 48px; }
  .holder-name {
    color: var(--brand-blue);
    font-weight: 700;
    font-size: 25px;
    letter-spacing: 0.5px;
    text-transform: uppercase;
  }
  .holder-role {
    color: var(--ink-soft);
    font-size: 15px;
    margin-top: 3px;
    text-transform: uppercase;
  }
  .divider {
    position: absolute;
    left: 62px; right: 40px; top: 118px;
    height: 2px;
    background: var(--brand-navy);
  }
  .contact-list {
    position: absolute;
    left: 62px; top: 140px;
    list-style: none;
    font-size: 15px;
    color: var(--ink);
    line-height: 27px;
  }
  .contact-list li { display: flex; align-items: center; gap: 10px; }
  .contact-list svg { width: 14px; height: 14px; fill: var(--brand-navy); }
  .contact-list .web { color: var(--brand-blue); }

  .brand {
    display: flex;
    align-items: center;
    gap: 12px;
    font-weight: 800;
    text-transform: uppercase;
    letter-spacing: 2px;
    line-height: 1.05;
  }
  .brand-mark {
    width: 14px; height: 14px;
    background: currentColor;
    flex: none;
  }
  .brand-name { display: block; }

  .front-brand {
    position: absolute;
    right: 46px; top: 150px;
    color: var(--brand-blue);
    font-size: 30px;
    text-align: left;
  }
  .address {
    position: absolute;
    right: 46px; bottom: 40px;
    text-align: right;
    font-size: 15px;
    line-height: 22px;
    color: var(--ink);
  }

  /* Back */
  .card-back {
    background: linear-gradient(135deg, var(--brand-blue) 0%, var(--brand-blue-dark) 60%, #2c3588 100%);
    display: flex;
    flex-direction: column;
    align-items: center;
    justify-content: center;
    gap: 34px;
  }
  .back-map {
    position: absolute; inset: 30px 50px;
    background: radial-gradient(ellipse at center, rgba(255,255,255,0.06), rgba(255,255,255,0) 70%);
  }
  .back-brand {
    position: relative;
    color: var(--back-ink);
    font-size: 40px;
  }
  .back-web {
    position: relative;
    color: var(--back-ink);
    font-size: 16px;
    letter-spacing: 0.5px;
  }
</style>
</head>
<body>
  <section class="card card-front" aria-label="Business card front">
    <svg class="front-swoosh" viewBox="0 0 700 400" preserveAspectRatio="none" aria-hidden="true">
      <path d="M0 240 C120 330 260 330 410 350 C470 358 500 380 520 400 L0 400 Z" fill="var(--grey-band)"/>
      <path d="M0 250 C120 340 250 345 400 365 C450 372 475 386 492 400 L0 400 Z" fill="#fff"/>
      <path d="M0 262 C120 350 250 356 390 376 C430 382 450 392 462 400 L0 400 Z" fill="var(--brand-blue)"/>
      <circle cx="0" cy="70" r="26" fill="var(--brand-blue)"/>
    </svg>
    <div class="holder">
      <p class="holder-name">Paul Dunmore</p>
      <p class="holder-role">Owner</p>
    </div>
    <div class="divider"></div>
    <ul class="contact-list">
      <li><svg viewBox="0 0 24 24"><path d="M6.6 10.8a15 15 0 0 0 6.6 6.6l2.2-2.2c.3-.3.7-.4 1-.2 1.1.4 2.3.6 3.6.6.6 0 1 .4 1 1V20c0 .6-.4 1-1 1A17 17 0 0 1 3 4c0-.6.4-1 1-1h3.5c.6 0 1 .4 1 1 0 1.3.2 2.5.6 3.6.1.3 0 .7-.2 1z"/></svg>(000)555-0142</li>
      <li><svg viewBox="0 0 24 24"><path d="M2 5h20v14H2z M2 5l10 8 10-8"/></svg>paul@dunmoreroofing-example.com</li>
      <li class="web"><svg viewBox="0 0 24 24"><circle cx="12" cy="12" r="10"/></svg>www.dunmoreroofing-example.com</li>
    </ul>
    <div class="brand front-brand">
      <span class="brand-mark"></span>
      <p class="brand-name">Dunmore<br>Roofing</p>
    </div>
    <p class="address">4172 Township road 43<br>Ridgeview, ON K9X4T2</p>
  </section>

  <section class="card card-back" aria-label="Business card back">
    <div class="back-map" role="img" aria-label="Faint dotted world map in the background"></div>
    <div class="brand back-brand">
      <span class="brand-mark"></span>
      <p class="brand-name">Dunmore<br>Roofing</p>
    </div>
    <p class="back-web">www.dunmoreroofing-example.com</p>
  </section>
</body>
</html>
```